Stylish Business Cards Wanted

- DOUBLE SIDED Design Required -

High end, edgy cards for a corporate and personal stylist. Must include logo,
Name: Belinda Harwick
Title: Director and Stylist
telephone : +61 8 7142 5809
email: belinda@theloombriefing.example
website: theloombriefing.example
Tag: Corporate Workwear & Uniform Specialist | Personal Stylist
Would like nice icons for telephone, email, website

Target Market(s)

Businesses wanting stylish uniforms, people wanting stylish wardrobes

Industry/Entity Type

Corporate Workwear Stylist

Contact Information for Business Card

I would like black, white and gold foiling incorporated in the design - possibly a touch of the other colours on my branding guide attached Name: Belinda Harwick Title: Director and Stylist telephone : +61 8 7142 5809 email: belinda@theloombriefing.example website: theloombriefing.example Tag: Corporate Workwear & Uniform Specialist | Personal Stylist Would like nice icons for telephone, email, website

Font styles to use
Other font styles liked:
• Raleway

Colors

Designer to choose colors to be used in the design.

Requirements
Must have
• Gold foil accents

```html
<!DOCTYPE html>
<html lang="en">
<head>
<meta charset="utf-8">
<title>The Loom Briefing — Business Card</title>
<link rel="stylesheet" href="https://fonts.googleapis.com/css2?family=Open+Sans:wght@400;700&display=swap">
<style>
  :root {
    --backdrop: #3a3a3a;
    --card-black: #1b1b1b;
    --gold-foil: #e8b940;
    --gold-edge: #c9a038;
    --text-white: #ecebe8;
    --gloss-black: #4a4a4a;
  }
  * { box-sizing: border-box; margin: 0; padding: 0; }
  html, body {
    width: 1200px; height: 801px; overflow: hidden;
    background: var(--backdrop);
    font-family: "Open Sans", Arial, sans-serif;
  }
  .sheet {
    width: 1200px; height: 801px;
    display: flex; align-items: center; justify-content: center; gap: 40px;
  }
  .card {
    position: relative;
    width: 520px; height: 317px;
    background: var(--card-black);
    border: 2px solid var(--gold-edge);
  }
  /* Front side */
  .card-front .identity {
    position: absolute; left: 40px; top: 90px; width: 190px;
    text-align: right;
  }
  .name {
    color: var(--gold-foil); font-weight: 700; font-size: 21px;
    letter-spacing: 0.5px; text-transform: uppercase; line-height: 1.2;
  }
  .title { color: var(--text-white); font-size: 14px; margin-top: 4px; }
  .divider {
    position: absolute; left: 248px; top: 78px;
    width: 1.5px; height: 80px; background: var(--gold-foil);
  }
  .contact-list {
    position: absolute; left: 266px; top: 80px;
    list-style: none; color: var(--text-white); font-size: 12.5px;
  }
  .contact-list li { display: flex; align-items: center; gap: 7px; line-height: 24px; }
  .contact-list svg { width: 12px; height: 12px; fill: var(--gold-foil); flex: none; }
  .tagline {
    position: absolute; left: 0; right: 0; bottom: 46px;
    text-align: center; color: var(--text-white); font-size: 14px;
  }
  .tagline .dot { color: var(--gold-foil); margin: 0 8px; }
  /* Back side */
  .card-back { display: flex; align-items: center; justify-content: center; }
  .brand-name {
    color: var(--gloss-black); font-weight: 700; font-size: 34px;
    letter-spacing: 3px; text-transform: uppercase;
  }
</style>
</head>
<body>
<main class="sheet">
  <section class="card card-front" aria-label="Card front">
    <div class="identity">
      <h1 class="name">Belinda Harwick</h1>
      <p class="title">Director and Stylist</p>
    </div>
    <div class="divider"></div>
    <ul class="contact-list">
      <li>
        <svg viewBox="0 0 24 24" aria-hidden="true"><path d="M6.6 10.8a15.1 15.1 0 0 0 6.6 6.6l2.2-2.2c.3-.3.7-.4 1-.2 1.1.4 2.3.6 3.6.6.6 0 1 .4 1 1V20c0 .6-.4 1-1 1A17 17 0 0 1 3 4c0-.6.4-1 1-1h3.5c.6 0 1 .4 1 1 0 1.3.2 2.5.6 3.6.1.3 0 .7-.2 1z"/></svg>
        +61 8 7142 5809
      </li>
      <li>
        <svg viewBox="0 0 24 24" aria-hidden="true"><path d="M2 5h20v14H2z M2 5l10 8 10-8" fill="var(--gold-foil)" stroke="var(--card-black)" stroke-width="1.5"/></svg>
        belinda@theloombriefing.example
      </li>
      <li>
        <svg viewBox="0 0 24 24" aria-hidden="true"><circle cx="12" cy="12" r="10"/><path d="M2 12h20M12 2c3 3 3 17 0 20M12 2c-3 3-3 17 0 20" fill="none" stroke="var(--card-black)" stroke-width="1.5"/></svg>
        theloombriefing.example
      </li>
    </ul>
    <p class="tagline">Corporate Workwear &amp; Uniform Specialist<span class="dot">•</span>Personal Stylist</p>
  </section>

  <section class="card card-back" aria-label="Card back">
    <p class="brand-name">The Loom Briefing</p>
  </section>
</main>
</body>
</html>
```